New Business Card Design Project

I need a design for business cards, i am an electrical business called "Corvane Electrical and Communications" i need the cards to be double sided with the company logo on the back (attached) the front needs to say my company name, web site, email address, telephone number, and ABN number and electrical license number. I am open to different arrangements of the information but would like the background to be incorporating something electrical or something that looks smart. open to all additional ideas also.

The company colours are orange and grey see logo attached.

Business Name: Corvane Electrical and Communications
Website: corvaneelectricalandcomms.example.com.au
Email: brent@corvaneelectricalandcomms.example.com.au
Telephone(mobile): 0481209736
ABN: 71208349162
Lic No: 418273D

Target Market(s)

Business entities, Project Managers, Accounts, Clients

Industry/Entity Type

Electrician

Contact Information for Business Card

I need a design for business cards, i am an electrical business called "Corvane Electrical and Communications" i need the cards to be double sided with the company logo on the back (attached) the front needs to say my company name

Font styles to use
Serif
Sans Serif

Colors
f37122
5c5c5c

Requirements
Must have
• Must have the Logo on the back open to different ways of it being on the back but had in mind to keep it central but again open to other options
Nice to have
• A real modern cool background that is eye catching yet contemporary
Should not have
• No backgrounds of a light bulb or plug or anything like that

```html
<!DOCTYPE html>
<html lang="en">
<head>
<meta charset="utf-8">
<title>Corvane Electrical and Communications – Business Cards</title>
<link rel="stylesheet" href="https://fonts.googleapis.com/css2?family=Open+Sans:wght@400;600;700&display=swap">
<style>
  :root {
    --orange: #f5a31a;
    --orange-deep: #f37122;
    --grey: #5c5c5c;
    --grey-light: #d9d9d9;
    --card-dark-1: #3b3b3b;
    --card-dark-2: #595959;
    --card-light: #ffffff;
    --stage: #e6e6e6;
  }
  * { box-sizing: border-box; margin: 0; padding: 0; }
  html, body {
    width: 1200px;
    height: 950px;
    overflow: hidden;
    background: var(--stage);
    font-family: "Open Sans", Arial, sans-serif;
  }
  .sheet {
    position: relative;
    width: 1200px;
    height: 950px;
  }
  .card {
    position: absolute;
    left: 250px;
    width: 700px;
    height: 428px;
    border-radius: 6px;
    box-shadow: 0 6px 18px rgba(0,0,0,0.18);
    overflow: hidden;
  }

  /* Back side */
  .card-back {
    top: 37px;
    background: linear-gradient(135deg, var(--card-dark-1), var(--card-dark-2));
  }
  .brand {
    position: absolute;
    top: 170px;
    left: 0;
    right: 0;
    display: flex;
    align-items: center;
    justify-content: center;
    gap: 14px;
  }
  .brand-dot {
    width: 22px;
    height: 22px;
    border-radius: 50%;
    background: var(--orange);
  }
  .brand-name {
    font-size: 28px;
    font-weight: 600;
    color: var(--grey-light);
    letter-spacing: 0.5px;
  }
  .back-web {
    position: absolute;
    top: 262px;
    left: 0;
    right: 0;
    text-align: center;
    font-size: 17px;
    color: var(--grey-light);
    opacity: 0.8;
  }

  /* Front side */
  .card-front {
    top: 485px;
    background: var(--card-light);
  }
  .person {
    position: absolute;
    top: 58px;
    left: 300px;
  }
  .person-name {
    font-size: 24px;
    font-weight: 700;
    color: var(--orange);
    letter-spacing: 0.5px;
  }
  .person-role {
    font-size: 16px;
    color: var(--grey);
    letter-spacing: 0.5px;
  }
  .cable-graphic {
    position: absolute;
    top: 130px;
    left: 130px;
    width: 480px;
    height: 120px;
    border-radius: 60px;
    background: linear-gradient(90deg, rgba(245,163,26,0.9), rgba(245,163,26,0.25));
  }
  .contact {
    position: absolute;
    left: 60px;
    right: 40px;
    top: 290px;
    font-size: 15px;
    color: var(--grey);
    line-height: 1.75;
    white-space: nowrap;
  }
  .contact-line {
    display: flex;
    align-items: center;
    gap: 8px;
  }
  .contact-line.ids { padding-left: 24px; }
  .icon { width: 16px; height: 16px; flex: none; }
  .icon path, .icon rect, .icon circle { fill: var(--orange); }
  .gap { width: 12px; flex: none; }
</style>
</head>
<body>
<main class="sheet">
  <section class="card card-back" aria-label="Card back">
    <div class="brand">
      <span class="brand-dot"></span>
      <span class="brand-name">Corvane Electrical and Communications</span>
    </div>
    <p class="back-web">corvaneelectricalandcomms.example.com.au</p>
  </section>

  <section class="card card-front" aria-label="Card front">
    <div class="person">
      <p class="person-name">BRENT CALLOWAY</p>
      <p class="person-role">PRESIDENT</p>
    </div>
    <div class="cable-graphic" role="img" aria-label="Orange electrical cable curving in a wave across the card"></div>
    <div class="contact">
      <p class="contact-line ids">ABN: 71208349162 | Lic No: 418273D</p>
      <p class="contact-line">
        <svg class="icon" viewBox="0 0 16 16" aria-hidden="true"><rect x="4" y="0" width="8" height="16" rx="2"/></svg>
        <span>0481209736</span>
        <span class="gap"></span>
        <svg class="icon" viewBox="0 0 16 16" aria-hidden="true"><path d="M0 3h16v10H0z"/></svg>
        <span>brent@corvaneelectricalandcomms.example.com.au</span>
      </p>
      <p class="contact-line">
        <svg class="icon" viewBox="0 0 16 16" aria-hidden="true"><circle cx="8" cy="8" r="8"/></svg>
        <span>corvaneelectricalandcomms.example.com.au</span>
      </p>
    </div>
  </section>
</main>
</body>
</html>
```